Regional beer Falkmo-Bräu needs new labels for 33cl Beercans

We are looking for a creative and professional design for our 33cl beer can label. The can itself is all black, and the design should be mainly in yellow and black colors to stand out on the store shelf.
The size of the label should be 206 mm x 80 mm

*Details and requirements:*

1. brand identity and target group
- Our brand stands for handcrafted quality with a modern touch.
- The target group is young adults and beer connoisseurs who value unique taste and stylish design.

2. style and aesthetics:*
- The design should be modern and eye-catching, inspired by the labels of Lunda Brauerei Hamburg.
- We prefer a minimalist style with clean lines and contrasts.

3. typography:*
- Use modern, legible fonts.
- Use freely available fonts.
- The brand name and important information should be emphasized.

4. images and graphics
- The logo can be used in its entirety or in individual parts.
- Illustrations or icons that emphasize the uniqueness of our beer are welcome.

5 *Colors:*
- Main colors are yellow and black.
- Accents in other colors are possible, but should be used sparingly.

6th *Legal requirements:*
- The label must provide space for legal information such as alcohol content, origin and barcode.

7 *Technical details
- Final files should be in AI, afdesign or PDF format with a resolution of at least 300 dpi.
- The design should be created in CMYK color model.

8th *Inspiration and references:*
- Examples of labels that we like are those of Lunda Brauerei Hamburg. We like their clear structure and modern look.

9 *Additional information:*
- The bottling date is printed on the can or bottle afterwards.
- Special features of our beer, such as flavor or special ingredients, should be highlighted.

We look forward to your creative suggestions and hope that you will help us to design a label that perfectly represents our brand!

Target Market(s)

The target group is young adults and beer connoisseurs who value unique taste and stylish design.

Industry/Entity Type

Beverage

Colors

Designer to choose colors to be used in the design.

Requirements
Must have
• The design should be modern and eye-catching but minimalist style with clean lines and contrasts. should include the writing falkmo-bräu (attachment)

```html
<!DOCTYPE html>
<html lang="de">
<head>
<meta charset="utf-8">
<title>Falkmo-Bräu Helles – Dosenetikett</title>
<link href="https://fonts.googleapis.com/css2?family=Arimo:wght@700&family=Noto+Serif:wght@400;700&display=swap" rel="stylesheet">
<style>
  :root {
    --backdrop: #97aec4;
    --label-black: #231f20;
    --gold: #b8912f;
    --cream: #f8f0dc;
    --white: #ffffff;
    --ink: #111111;
    --fresh-green: #6cc04a;
    --warn-orange: #f39a2b;
    --alert-red: #e53a2f;
  }
  html, body {
    margin: 0;
    padding: 0;
    width: 899px;
    height: 1200px;
    overflow: hidden;
    background: var(--backdrop);
  }
  .stage {
    position: relative;
    width: 899px;
    height: 1200px;
  }
  .can-label {
    position: absolute;
    left: 48px;
    top: 381px;
    width: 802px;
    height: 438px;
    display: block;
  }
  .label-ground { fill: var(--label-black); }
  .gold-line { fill: none; stroke: var(--gold); stroke-width: 3; }
  .serif { font-family: "Noto Serif", Georgia, serif; }
  .brand-name { font-weight: 700; font-size: 84px; fill: var(--cream); }
  .beer-style { font-size: 74px; letter-spacing: 10px; fill: var(--gold); }
  .estd { font-size: 26px; fill: var(--gold); }
  .tagline { font-size: 20px; fill: var(--cream); letter-spacing: 0.5px; }
  .spec { font-size: 24px; fill: var(--cream); }
  .story { font-size: 28px; fill: var(--cream); }
  .brewery { font-size: 20px; fill: var(--cream); }
  .panel-frame { fill: none; stroke: var(--gold); stroke-width: 3; }
  .illustration-fill { fill: var(--gold); }
  .date-strip { fill: var(--white); }
  .date-text { font-family: "Arimo", Arial, sans-serif; font-weight: 700; font-size: 20px; fill: var(--ink); }
  .date-marker { fill: var(--ink); }
</style>
</head>
<body>
<main class="stage">
  <svg class="can-label" viewBox="0 0 1478 808" xmlns="http://www.w3.org/2000/svg" aria-label="Falkmo-Bräu Helles Etikett">
    <defs>
      <linearGradient id="freshness-scale" x1="0" y1="0" x2="0" y2="1">
        <stop offset="0" stop-color="var(--alert-red)"/>
        <stop offset="0.1" stop-color="var(--warn-orange)"/>
        <stop offset="0.22" stop-color="var(--fresh-green)"/>
        <stop offset="1" stop-color="var(--fresh-green)"/>
      </linearGradient>
    </defs>

    <rect class="label-ground" x="0" y="0" width="1478" height="808"/>

    <!-- front panel -->
    <g class="front-panel">
      <path class="gold-line" d="M334 118 C322 82 300 63 268 63 L101 63 Q51 63 51 113 L51 695 Q51 745 101 745 L218 745 Q238 745 238 722"/>
      <path class="gold-line" d="M334 118 C346 82 368 63 400 63 L567 63 Q617 63 617 113 L617 695 Q617 745 567 745 L450 745 Q430 745 430 722"/>
      <line class="gold-line" x1="290" y1="715" x2="290" y2="808"/>
      <line class="gold-line" x1="334" y1="715" x2="334" y2="808"/>
      <line class="gold-line" x1="378" y1="715" x2="378" y2="808"/>

      <g role="img" aria-label="Hopfendolde">
        <ellipse class="illustration-fill" cx="334" cy="163" rx="36" ry="48"/>
      </g>
      <text class="serif estd" x="288" y="174" text-anchor="end">ESTD</text>
      <text class="serif estd" x="382" y="174">2015</text>

      <text class="serif brand-name" x="334" y="334" text-anchor="middle">Falkmo-Bräu</text>
      <text class="serif beer-style" x="338" y="433" text-anchor="middle">HELLES</text>
      <text class="serif tagline" x="334" y="486" text-anchor="middle">HANDGEFERTIGT - UNGESCHMACKSFREI</text>
      <text class="serif tagline" x="334" y="526" text-anchor="middle">BAVARIAN STYLE</text>

      <g role="img" aria-label="Fünf Weizenähren">
        <rect class="illustration-fill" x="228" y="563" width="212" height="155" rx="18"/>
      </g>
      <text class="serif spec" x="96" y="692">4,8% VOL</text>
      <text class="serif spec" x="526" y="692" text-anchor="middle">33 CL</text>
    </g>

    <!-- story panel -->
    <g class="story-panel">
      <rect class="panel-frame" x="678" y="63" width="420" height="682"/>
      <text class="serif story" x="706" y="140">Von Hand gebraut, mit</text>
      <text class="serif story" x="706" y="174">Geduld und Präzision. 6</text>
      <text class="serif story" x="706" y="209">Wochen.</text>
      <text class="serif story" x="706" y="278">Ein Ziel: purer Geschmack.</text>
      <line class="gold-line" x1="706" y1="306" x2="1080" y2="306"/>
      <text class="serif story" x="706" y="347">Aus Pilsner Malz gebraut,</text>
      <text class="serif story" x="706" y="382">untergärig und mit</text>
      <text class="serif story" x="706" y="416">Aromahopfen verfeinert.</text>
      <line class="gold-line" x1="706" y1="444" x2="1080" y2="444"/>
      <line class="gold-line" x1="706" y1="631" x2="1080" y2="631"/>
      <text class="serif story" x="706" y="679">Aufbewahrungshinweis:</text>
      <text class="serif story" x="706" y="713">Kühl lagern, frisch servieren</text>
    </g>

    <!-- brewery details -->
    <g class="brewery-info">
      <text class="serif brewery" x="1126" y="593">Brauerei:</text>
      <text class="serif brewery" x="1126" y="623">Falkmo-Bräu</text>
      <text class="serif brewery" x="1126" y="652">Lindenweg 12</text>
      <text class="serif brewery" x="1126" y="682">CH-3300 Talwil</text>
      <text class="serif brewery" x="1126" y="712">www.falkmo-bräu.ch</text>
    </g>

    <!-- best-before strip -->
    <g class="best-before">
      <rect class="date-strip" x="1365" y="63" width="113" height="682"/>
      <text class="date-text" transform="translate(1398 229) rotate(-90)">W-LOS: W181</text>
      <text class="date-text" transform="translate(1398 711) rotate(-90)">Mindestens haltbar bis: 10.10.2025</text>
      <rect x="1418" y="96" width="26" height="613" fill="url(#freshness-scale)"/>
      <polygon class="date-marker" points="1418,352 1436,370 1418,388"/>
    </g>
  </svg>
</main>
</body>
</html>
```